Brightfield Ventures Inc. Letterhead

Creation of attractive and eye catching letterhead for a business start-up for the construction industry. Letterhead must relate to construction, but avoid standard hammer and tools in the design.

I forgot to add some details, sorry about that. Some pertinent info: Ph: 916-555-0187 brightfieldventures.example 448 Willowmere Ave, Ste 210 Folsom, CA 95999 info@brightfieldventures.example not sure if slogan should be in there" “Connecting construction professionals to create a purpose driven industry.” must be able to be used in word. Thanks!

```html
<!DOCTYPE html>
<html lang="en">
<head>
<meta charset="utf-8">
<title>Brightfield Ventures Inc. Letterhead</title>
<link href="https://fonts.googleapis.com/css2?family=Arimo:wght@700&family=Source+Sans+3:wght@400;600&display=swap" rel="stylesheet">
<style>
  :root {
    --brand-red: #b70909;
    --band-grey: #3d3d3f;
    --ink: #2b2b2b;
    --body-ink: #444446;
    --navy: #1f2a5c;
    --paper: #fbfbfb;
    --backdrop: #e9e9e9;
    --rule: #cfcfcf;
    --sig-tone: #e4e4e4;
  }
  * { box-sizing: border-box; margin: 0; padding: 0; }
  html, body { width: 1200px; height: 1200px; overflow: hidden; background: var(--backdrop); }
  .sheet-frame { position: absolute; left: 196px; top: 30px; width: 808px; height: 1140px; }
  .letterhead {
    position: absolute; left: 0; top: 0; width: 925px; height: 1305px;
    transform: scale(0.8736); transform-origin: 0 0;
    background: var(--paper);
    box-shadow: 0 2px 10px rgba(0,0,0,0.15);
    overflow: hidden;
    font-family: "Source Sans 3", "Myriad Pro", sans-serif;
  }
  .header-swoosh { position: absolute; left: 0; top: 0; width: 925px; height: 230px; }
  .brand-name {
    position: absolute; left: 60px; top: 150px; width: 220px;
    text-align: center; color: var(--navy);
    font-weight: 600; font-size: 26px; line-height: 30px; letter-spacing: 0.5px;
  }
  .header-divider { position: absolute; left: 291px; top: 72px; width: 1px; height: 122px; background: var(--rule); }
  .contact-block { position: absolute; left: 311px; top: 86px; color: var(--ink); font-size: 13.5px; line-height: 17.5px; }
  .contact-line { display: flex; align-items: center; gap: 5px; }
  .contact-line svg { width: 11px; height: 11px; flex: none; }
  .postal { margin-top: 11px; line-height: 19px; }
  .greeting {
    position: absolute; left: 79px; top: 314px;
    font-family: "Arimo", Arial, sans-serif; font-weight: 700; font-size: 20px; color: var(--ink);
  }
  .letter-body { position: absolute; left: 80px; top: 368px; width: 765px; color: var(--body-ink); font-size: 19.3px; line-height: 24.2px; }
  .letter-body p { text-align: justify; margin-bottom: 24px; }
  .signature-area { position: absolute; left: 80px; top: 930px; width: 146px; height: 68px; background: var(--sig-tone); border-radius: 4px; }
</style>
</head>
<body>
<div class="sheet-frame">
  <div class="letterhead">
    <svg class="header-swoosh" viewBox="0 0 925 230" aria-hidden="true">
      <path fill="var(--brand-red)" d="M0,0 H925 V178 C760,108 470,5 210,14 C110,18 35,48 0,85 Z"/>
      <path fill="var(--band-grey)" d="M30,66 C80,38 150,22 215,21 C470,16 760,112 925,180 V216 C760,140 470,30 215,26 C150,26 85,42 30,66 Z"/>
    </svg>

    <div class="brand-name">Brightfield Ventures</div>
    <div class="header-divider"></div>

    <div class="contact-block">
      <div class="contact-line">
        <svg viewBox="0 0 12 12"><path fill="var(--brand-red)" d="M2.5 0.8 L4.4 2.9 L3.4 4.2 C4 5.8 5.6 7.5 7.4 8.4 L8.7 7.3 L11 9.2 L9.8 11.2 C5.5 11 1 6.5 0.8 2.2 Z"/></svg>
        <span>1-254-555-0143</span>
      </div>
      <div class="contact-line">
        <svg viewBox="0 0 12 12"><rect x="1" y="3" width="10" height="7" fill="var(--brand-red)"/><path d="M1.5 3.5 L6 7 L10.5 3.5" stroke="#fff" stroke-width="1" fill="none"/></svg>
        <span>info@companyname.example</span>
      </div>
      <div class="contact-line">
        <svg viewBox="0 0 12 12"><circle cx="6" cy="6" r="5" fill="var(--brand-red)"/><path d="M1 6 H11 M6 1 V11 M2 3.5 H10 M2 8.5 H10" stroke="#fff" stroke-width="0.7"/><ellipse cx="6" cy="6" rx="2.2" ry="5" fill="none" stroke="#fff" stroke-width="0.7"/></svg>
        <span>www.companyname.example</span>
      </div>
      <div class="postal">Po. box 201, Street Name,<br>City Name, Zip Code - 00000</div>
    </div>

    <div class="greeting">Dear Mr. Hale,</div>

    <div class="letter-body">
      <p>Lorem Ipsum is simply dummy text of the printing and typesetting industry. Lorem Ipsum has been the industry's standard dummy text ever since the 1500s, when an unknown printer took a galley of type and scrambled it to make a type specimen book. It has survived not only five centuries, but also the leap into electronic typesetting, remaining essentially unchanged.</p>
      <p>The standard chunk of Lorem Ipsum used since the 1500s is reproduced below for those interested. Sections 1.10.32 and 1.10.33 from "de Finibus Bonorum et Malorum" by Cassius are also reproduced in their exact original form, accompanied by English versions from the 1914 translation by H. Ramsey</p>
      <p>Lorem Ipsum is simply dummy text of the printing and typesetting industry. Lorem Ipsum has been the industry's standard dummy text ever since the 1500s, when an unknown printer took a galley of type and scrambled it to make a type specimen book. It has survived not only five centuries, but also the leap into electronic typesetting, remaining essentially unchanged. It was popularised in the</p>
      <p>The standard chunk of Lorem Ipsum used since the 1500s is reproduced below for those interested. Sections 1.10.32 and 1.10.33 from "de Finibus Bonorum et Malorum" by Cassius are also reproduced in their exact original form, accompanied by English versions from the 1914 translation by H. Ramsey</p>
    </div>

    <div class="signature-area" role="img" aria-label="Handwritten signature of the sender"></div>
  </div>
</div>
</body>
</html>
```